Vantiqo custom business card design

Need a authentic, innovative business card design for a new mobile app business. I am uploading a few screen images from our app for you to view. I would like app design theme to match business card design. I can also send logo images.

```html
<!DOCTYPE html>
<html lang="en">
<head>
<meta charset="utf-8">
<title>Vantiqo Business Card</title>
<link rel="stylesheet" href="https://fonts.googleapis.com/css2?family=Open+Sans:wght@400;600;700;800&display=swap">
<style>
  :root {
    --backdrop: #3b3430;
    --card: #1e1f21;
    --card-edge: #111213;
    --purple: #6c1fae;
    --white: #ffffff;
    --text-soft: #e9e9ec;
    --emboss: #3a3b3e;
    --emboss-text: #6d6e72;
    --divider: #8b8c90;
  }
  * { box-sizing: border-box; margin: 0; padding: 0; }
  html, body {
    width: 1200px; height: 864px; overflow: hidden;
    background: var(--backdrop);
    font-family: "Open Sans", sans-serif;
  }
  .canvas {
    width: 1200px; height: 864px;
    display: flex; flex-direction: column; align-items: center; justify-content: center;
    gap: 40px;
  }
  .card {
    width: 640px; height: 366px;
    background: var(--card);
    border-radius: 4px;
    box-shadow: 0 14px 30px rgba(0,0,0,.45), 0 0 0 1px var(--card-edge);
    position: relative;
  }
  /* Front */
  .card--front {
    display: flex; flex-direction: column; align-items: center; justify-content: center;
  }
  .front-mark { display: flex; align-items: center; gap: 14px; }
  .front-mark__dot {
    width: 54px; height: 54px; border-radius: 50%;
    background: var(--emboss);
  }
  .front-mark__name {
    font-weight: 800; font-size: 46px; color: var(--emboss-text); letter-spacing: .5px;
  }
  .front-url {
    margin-top: 34px;
    font-size: 15px; letter-spacing: 8px; color: var(--text-soft);
  }
  /* Back */
  .card--back { display: flex; align-items: center; }
  .brand {
    width: 300px; display: flex; flex-direction: column; align-items: center; gap: 16px;
  }
  .brand__dot {
    width: 120px; height: 120px; border-radius: 50%; background: var(--purple);
  }
  .brand__name { font-weight: 800; font-size: 46px; color: var(--white); }
  .divider {
    width: 1px; height: 230px;
    background: linear-gradient(to bottom, transparent, var(--divider) 20%, var(--divider) 80%, transparent);
  }
  .contact { padding-left: 34px; color: var(--text-soft); font-size: 16px; line-height: 1.3; }
  .contact__name { color: var(--purple); font-weight: 700; font-size: 20px; text-transform: uppercase; }
  .contact__role { text-transform: uppercase; font-size: 16px; margin-bottom: 6px; }
  .contact__address { margin-bottom: 6px; }
  .contact__list { list-style: none; }
  .contact__list li { display: flex; align-items: center; gap: 10px; }
  .contact__list svg { width: 14px; height: 14px; fill: var(--purple); flex: none; }
  .contact__list .no-icon { padding-left: 24px; }
</style>
</head>
<body>
<main class="canvas">
  <section class="card card--front" aria-label="Card front">
    <div class="front-mark">
      <span class="front-mark__dot"></span>
      <span class="front-mark__name">Vantiqo</span>
    </div>
    <p class="front-url">www.vantiqo.com</p>
  </section>

  <section class="card card--back" aria-label="Card back">
    <div class="brand">
      <span class="brand__dot"></span>
      <span class="brand__name">Vantiqo</span>
    </div>
    <div class="divider"></div>
    <div class="contact">
      <p class="contact__name">Mara Velden</p>
      <p class="contact__role">President</p>
      <p class="contact__address">2417 Harrow Lane<br>Eastbrook, NY 11042</p>
      <ul class="contact__list">
        <li><svg viewBox="0 0 16 16"><path d="M3 1h3l1.5 4-2 1.2a9 9 0 0 0 4.3 4.3L11 8.5l4 1.5v3a2 2 0 0 1-2 2A12 12 0 0 1 1 3a2 2 0 0 1 2-2z"/></svg>555 0147 2281</li>
        <li><svg viewBox="0 0 16 16"><path d="M4 0h8a1 1 0 0 1 1 1v14a1 1 0 0 1-1 1H4a1 1 0 0 1-1-1V1a1 1 0 0 1 1-1zm1 2v10h6V2zm3 11a1 1 0 1 0 0 2 1 1 0 0 0 0-2z"/></svg>555 0193 4462</li>
        <li><svg viewBox="0 0 16 16"><path d="M4 0h6l2 2v4h2a1 1 0 0 1 1 1v7a1 1 0 0 1-1 1H2a1 1 0 0 1-1-1V7a1 1 0 0 1 1-1h2zm1 1v5h6V3H9V1zm5 8v2h2V9z"/></svg>555 0128 7735</li>
        <li><svg viewBox="0 0 16 16"><path d="M0 3h16v1L8 9 0 4zm0 3 8 5 8-5v7H0z"/></svg>mara@vantiqo.com</li>
        <li><svg viewBox="0 0 16 16"><path d="M8 0a8 8 0 1 0 0 16A8 8 0 0 0 8 0zm0 1.5c.9 0 2 1.8 2.3 5H5.7C6 3.3 7.1 1.5 8 1.5zM1.6 7.5h2.6c0-1.7.4-3.2.9-4.3a6.5 6.5 0 0 0-3.5 4.3zm0 1h2.6c0 1.7.4 3.2.9 4.3a6.5 6.5 0 0 1-3.5-4.3zm4.1 0h4.6c-.3 3.2-1.4 6-2.3 6s-2-2.8-2.3-6zm6.1-1h2.6a6.5 6.5 0 0 0-3.5-4.3c.5 1.1.9 2.6.9 4.3zm0 1c0 1.7-.4 3.2-.9 4.3a6.5 6.5 0 0 0 3.5-4.3z"/></svg>www.vantiqo.com</li>
      </ul>
    </div>
  </section>
</main>
</body>
</html>
```